business card deign

Logo needs the following on it.
1. attached logo
2. Tagline - "From the cooler to the crowd...we keep it rolling!"
3. Name- Dalton Pikes, Founder and CPO
4. Address - 412 E. Carver Avenue, Ste 2207, Tampa, FL. 33917
5. Phone - 555.318.4726

```html
<!DOCTYPE html>
<html lang="en">
<head>
<meta charset="utf-8">
<title>Chillbay Business Card</title>
<link href="https://fonts.googleapis.com/css2?family=Montserrat:wght@400;600;700&family=Roboto:wght@700&display=swap" rel="stylesheet">
<style>
  :root {
    --stage: #3a3a3a;
    --ink: #0c0c0c;
    --paper: #ffffff;
    --card-dark: #161616;
    --muted: #3c3c3c;
    --pattern-a: #2a2a2a;
    --pattern-b: #101010;
  }
  * { margin: 0; padding: 0; box-sizing: border-box; }
  html, body { width: 1200px; height: 875px; overflow: hidden; }
  body {
    background: var(--stage);
    font-family: "Montserrat", sans-serif;
    position: relative;
  }
  .card {
    position: absolute;
    top: 282px;
    width: 540px;
    height: 310px;
    border-radius: 18px;
    overflow: hidden;
  }
  /* Back side */
  .card-back { left: 40px; background: var(--card-dark); }
  .card-back .pattern {
    position: absolute; inset: 0;
    background: linear-gradient(135deg, var(--pattern-a) 0%, var(--pattern-b) 70%);
  }
  .card-back .brand {
    position: absolute; left: 0; right: 0; top: 140px;
    text-align: center;
    font-family: "Roboto", sans-serif;
    font-weight: 700; font-size: 22px;
    letter-spacing: 14px;
    color: var(--paper);
  }
  /* Front side */
  .card-front { left: 620px; background: var(--paper); color: var(--ink); }
  .person { position: absolute; left: 36px; top: 88px; }
  .person-name { font-weight: 700; font-size: 20px; }
  .person-role { font-size: 11px; color: var(--muted); margin-top: 2px; }
  .address {
    position: absolute; left: 36px; top: 172px;
    font-size: 11px; line-height: 15px; color: var(--muted);
  }
  .contacts {
    position: absolute; left: 36px; top: 216px;
    list-style: none; font-size: 11px; color: var(--muted);
  }
  .contacts li { display: flex; align-items: center; gap: 8px; height: 17px; }
  .contacts svg { width: 10px; height: 10px; fill: var(--ink); }
  .mascot-art {
    position: absolute; left: 352px; top: 24px;
    width: 116px; height: 126px;
    background: linear-gradient(180deg, #1a1a1a, #000);
    border-radius: 40px 40px 4px 4px;
  }
  .logo-bar {
    position: absolute; left: 300px; right: 0; top: 150px;
    height: 14px; background: var(--ink);
  }
  .logo-word {
    position: absolute; left: 300px; right: 0; top: 172px;
    text-align: center;
    font-family: "Montserrat", sans-serif;
    font-weight: 700; font-size: 26px; letter-spacing: 8px;
    color: var(--ink);
  }
  .tagline-band {
    position: absolute; left: 190px; right: 0; top: 236px;
    height: 24px; background: var(--ink);
    color: var(--paper);
    font-weight: 700; font-size: 11px;
    display: flex; align-items: center; justify-content: flex-end;
    padding-right: 18px;
    white-space: nowrap;
  }
  .base-line {
    position: absolute; left: 0; right: 0; top: 282px;
    height: 8px; background: var(--ink);
  }
</style>
</head>
<body>
  <section class="card card-back">
    <div class="pattern" role="img" aria-label="Repeating pattern of the brand mascot silhouette in glossy black tones"></div>
    <div class="brand">CHILLBAY</div>
  </section>

  <section class="card card-front">
    <div class="person">
      <div class="person-name">Dalton Pikes</div>
      <div class="person-role">Founder and CPO</div>
    </div>
    <div class="address">412 E. Carver Avenue, Ste 2207,<br>Tampa, FL. 33917</div>
    <ul class="contacts">
      <li><svg viewBox="0 0 10 10"><path d="M2 0.5 L4 2.8 L3 4 Q4.2 6 6 7 L7.2 6 L9.5 8 L8.2 9.5 Q3.5 9 0.5 1.8 Z"/></svg>555.318.4726</li>
      <li><svg viewBox="0 0 10 10"><path d="M0 2 H10 V8.5 H0 Z M0.8 2.6 L5 5.6 L9.2 2.6" stroke="#fff" stroke-width="0.8"/></svg>info@chillbay.com</li>
      <li><svg viewBox="0 0 10 10"><circle cx="5" cy="5" r="4.6"/><path d="M0.6 5 H9.4 M5 0.5 Q2.4 5 5 9.5 Q7.6 5 5 0.5" stroke="#fff" stroke-width="0.7" fill="none"/></svg>www.chillbay.com</li>
    </ul>
    <div class="mascot-art" role="img" aria-label="Black silhouette of the brand mascot standing upright"></div>
    <div class="logo-bar"></div>
    <div class="logo-word">CHILLBAY</div>
    <div class="tagline-band">From the cooler to the crowd...we keep it rolling</div>
    <div class="base-line"></div>
  </section>
</body>
</html>
```